Wordpress Web Design & Coding for velcorahealth.ca

We need a website for a new investment company that is visually grabbing and vibrant. We would like to see a web page that displays trust, growth and confidence. Needs to be responsive and mobile friendly for all browsers and coded for both Android & IOS.

Open to the number of pages and menu items. I selected 4 but if you feel the layout would work better with less I am open to this. Need to sell the people (management team/related businesses) and then show where the invested money will be going (upcoming projects).

Company Info:

Vel Cora is an investment company put together by a group of seasoned business professionals who have come together to combine decades of success in the real estate development, management, financing and medical services. The company will be a full service company offering turn key solutions for medical professionals.

Vel-Cora will focus on providing a full range of services via a group of distinct companies to deliver newly emerging needs of the medical community. The end goal will be to create complete solutions for individuals in the medical community. Our group has experience and success with the conceptualization, construction and financing of medical and dental clinic spaces. Vel-Cora Solutions will be established to accommodate all areas of the development and creation of clinics for medical professionals from building construction to equipment financing and administrations.

You can mention these companies and take photos from their websites. You can also use stock photos.

Our construction partner:
https://318bld.com/projects/

Our equipment leasing partner:
https://www.norvixa.com/

Our Management Team and medical partners

Gil Parish
https://www.ourfirmstance.ca/

Dietmar Vellasquin
https://www.gshdentalservices.com/about-us

PROPOSED PROJECTS (see attachment for details)
Pinegrove Business Park
Holtmere Business Park
Mt. Corwin Ridge Professional

Target Market(s)

Investors

Industry/Entity Type

Investment

Coding

Coded - Design and coding required

Number of Pages Required

4 page

Font styles to use
Sans Serif

Requirements
Must have
• Wordpress – must be both desktop and mobile friendly with fast page load speed
Ability to edit after ourselves in Wordpress
Attractive home page with logo etc.
Logo colours are: for the blue the pantone color is #0355a3
and for the green is #8cc63f

Sections, about us, what we do/services we provide, contact us

```html
<!DOCTYPE html>
<html lang="en">
<head>
<meta charset="utf-8">
<title>Vel-Cora Solutions</title>
<link href="https://fonts.googleapis.com/css2?family=Montserrat:wght@400;500;600;700&family=Roboto+Condensed:wght@700&display=swap" rel="stylesheet">
<style>
:root{
  --blue:#0355a3;
  --blue-dark:#0a3f86;
  --green:#8cc63f;
  --sky:#d3e4fb;
  --text:#555b66;
  --white:#ffffff;
}
*{margin:0;padding:0;box-sizing:border-box}
html,body{width:1200px;height:4161px;overflow:hidden}
body{position:relative;font-family:'Montserrat',sans-serif;color:var(--text);background:var(--white)}
.abs{position:absolute}
.brand{color:var(--blue);font-weight:700;line-height:1.05;text-align:center}
/* header */
.site-header{left:0;top:0;width:1200px;height:110px;background:var(--white);border-bottom:1px solid #e4e8ee}
.site-header .brand{left:142px;top:38px;font-size:22px}
.site-header .brand small{display:block;font-size:12px;letter-spacing:2px}
.nav a{position:absolute;top:50px;font-size:13px;color:#333;text-decoration:none;font-weight:500}
.nav .active{color:var(--blue)}
.btn-contact{left:929px;top:40px;width:130px;height:34px;border-radius:17px;background:var(--green);color:var(--white);font-size:13px;display:flex;align-items:center;justify-content:center;box-shadow:0 3px 6px rgba(0,0,0,.15)}
/* hero */
.hero{left:0;top:110px;width:1200px;height:458px;
  background:
    radial-gradient(ellipse 160px 200px at 240px 290px,rgba(236,196,170,.85),rgba(236,196,170,0) 70%),
    radial-gradient(ellipse 260px 230px at 230px 160px,rgba(255,255,255,.75),rgba(255,255,255,0) 70%),
    radial-gradient(ellipse 300px 160px at 560px 120px,rgba(240,246,252,.9),rgba(240,246,252,0) 70%),
    radial-gradient(ellipse 420px 300px at 960px 300px,rgba(52,98,168,.55),rgba(52,98,168,0) 75%),
    linear-gradient(180deg,rgba(255,255,255,0) 60%,rgba(210,222,236,.8) 100%),
    linear-gradient(100deg,#d8e2ec 0%,#b9cde3 30%,#8fb0d4 60%,#6f96c6 80%,#a9c3df 100%)}
.hero-panel{left:694px;top:242px;width:396px;height:150px;background:rgba(150,176,210,.4)}
.hero-title{left:600px;top:249px;width:458px;text-align:right;font-family:'Roboto Condensed',sans-serif;font-weight:700;font-size:21.5px;line-height:34px;color:var(--white);text-shadow:0 2px 3px rgba(0,0,0,.35);white-space:nowrap}
/* buttons */
.pill{display:flex;align-items:center;border-radius:22px;background:var(--blue);color:var(--white);font-weight:600;font-size:13px;box-shadow:0 4px 8px rgba(3,85,163,.3)}
.pill .ico{width:40px;height:40px;border-radius:50%;background:var(--white);display:flex;align-items:center;justify-content:center;margin-right:18px;flex:none;box-shadow:0 2px 5px rgba(0,0,0,.2)}
.pill.green{background:var(--green);box-shadow:none}
.pill.sm{font-size:11px;height:30px}
.pill.sm .ico{width:30px;height:30px;margin-right:12px}
/* about */
.section-title{font-weight:700;color:var(--blue);font-size:29px;letter-spacing:.5px}
.about-title{left:142px;top:642px}
.about-title span{color:var(--green)}
.about-copy{left:142px;top:702px;font-size:11.8px;line-height:23px;letter-spacing:.55px;white-space:nowrap}
.about-copy p+p{margin-top:8px}
.about-copy u{color:var(--blue)}
.about-visual{left:680px;top:641px;width:378px;height:375px;border-radius:4px;
  background:
    radial-gradient(ellipse 120px 140px at 110px 170px,rgba(140,198,63,.55),rgba(140,198,63,0) 70%),
    radial-gradient(ellipse 140px 120px at 280px 110px,rgba(150,190,235,.7),rgba(150,190,235,0) 70%),
    radial-gradient(ellipse 110px 120px at 200px 290px,rgba(20,50,110,.6),rgba(20,50,110,0) 70%),
    linear-gradient(135deg,#3b7fcf,#0355a3 55%,#2d6cbc)}
/* solutions */
.solutions{left:0;top:1111px;width:1200px;height:1048px;border-radius:90px 0 90px 0;
  background:
    radial-gradient(ellipse 140px 380px at 620px 560px,rgba(120,160,215,.45),rgba(120,160,215,0) 70%),
    radial-gradient(ellipse 200px 500px at 80px 500px,rgba(255,255,255,.5),rgba(255,255,255,0) 70%),
    radial-gradient(ellipse 240px 420px at 1060px 620px,rgba(255,255,255,.45),rgba(255,255,255,0) 70%),
    linear-gradient(180deg,#d6e7fc,#c4daf7 60%,#d1e3fb)}
.center{left:0;width:1200px;text-align:center}
.svc-title{font-weight:600;color:#222;font-size:27px}
.svc-copy{font-size:13px;line-height:25.5px;letter-spacing:.6px;color:#4c5360;white-space:nowrap}
/* projects */
.card{width:290px;height:395px;background:var(--white);border-radius:22px;box-shadow:0 4px 14px rgba(0,0,0,.12);overflow:hidden}
.card .photo{height:182px}
.card .date{position:absolute;left:16px;top:198px;font-size:10.5px;color:#444}
.card .date i{display:inline-block;width:9px;height:9px;background:var(--green);margin-right:6px;border-radius:1px}
.card h3{position:absolute;left:16px;top:218px;font-size:14.5px;color:var(--blue);font-weight:700;white-space:nowrap}
.card p{position:absolute;left:16px;top:246px;width:258px;font-size:11.5px;line-height:21px;color:#555}
.card .pill{position:absolute;left:16px;top:338px;width:130px}
.arrow{width:44px;height:44px;border-radius:50%;background:var(--white);box-shadow:0 2px 8px rgba(0,0,0,.2);display:flex;align-items:center;justify-content:center}
/* team */
.team{left:0;top:2878px;width:1200px;height:575px;border-radius:90px 0 90px 0;
  background:
    radial-gradient(ellipse 160px 260px at 330px 140px,rgba(110,160,60,.55),rgba(110,160,60,0) 70%),
    radial-gradient(ellipse 260px 300px at 1050px 200px,rgba(180,220,120,.5),rgba(180,220,120,0) 70%),
    linear-gradient(180deg,#8dc63f,#84bf38)}
.tab{height:37px;border-radius:19px;display:flex;align-items:center;justify-content:center;font-size:13px;font-weight:600}
.person{width:435px;height:186px;background:var(--white);border-radius:14px;box-shadow:0 4px 12px rgba(0,0,0,.15)}
.person .portrait{position:absolute;left:0;top:10px;width:157px;height:170px}
.person h4{position:absolute;left:182px;top:30px;font-size:17px;color:#222;white-space:nowrap}
.person .role{position:absolute;left:182px;top:54px;font-size:11px;color:var(--blue)}
.person p{position:absolute;left:182px;top:75px;width:230px;font-size:11.5px;line-height:18px;color:#444}
.person .badge{position:absolute;left:182px;top:138px;width:104px;height:24px;background:#dfe3e8;border-radius:3px}
/* newsletter */
.news-input{left:302px;top:3635px;width:590px;height:47px;border-radius:24px;background:var(--white);box-shadow:inset 0 1px 4px rgba(0,0,0,.2);font-size:13px;color:#666;padding:15px 28px}
.news-btn{left:711px;top:3635px;width:181px;height:47px;border-radius:24px;background:var(--green);color:var(--white);font-size:13px;font-weight:600;display:flex;align-items:center;justify-content:center}
/* footer */
.site-footer{left:0;top:3763px;width:1200px;height:349px;background:var(--blue);border-radius:70px 0 0 0;color:var(--white)}
.site-footer .brand{color:var(--white);left:142px;top:90px;font-size:34px}
.site-footer .brand small{display:block;font-size:19px;letter-spacing:2px}
.foot-about{left:142px;top:198px;width:230px;font-size:11.5px;line-height:21px;letter-spacing:.6px}
.col-h{font-size:15px;font-weight:500}
.col-h::after{content:"";display:block;width:24px;height:2px;background:var(--green);margin-top:12px}
.list{font-size:12px;line-height:28px}
.list li{list-style:none}
.list li::before{content:"» ";}
.contact-row{font-size:12px;line-height:20px}
.social{display:flex;align-items:center;font-size:12.5px;height:40px}
.social i{width:26px;height:26px;border-radius:50%;background:#1570c6;margin-right:12px;display:inline-block}
.copyright{left:0;top:4112px;width:1200px;height:49px;background:var(--green);color:var(--white);font-size:12.5px;display:flex;align-items:center;justify-content:center}
</style>
</head>
<body>

<header class="site-header abs">
  <div class="brand abs">VEL-CORA<small>SOLUTIONS</small></div>
  <nav class="nav">
    <a class="active" style="left:568px">HOME</a>
    <a style="left:664px">ABOUT US</a>
    <a style="left:786px">WHAT WE DO</a>
  </nav>
  <div class="btn-contact abs">CONTACT US</div>
</header>

<section class="hero abs" role="img" aria-label="Doctor touching a floating panel of medical icons in a bright clinic corridor"></section>
<div class="hero-panel abs"></div>
<h1 class="hero-title abs">Vel-Cora Is An Investment Company<br>With Focus on Providing A Full Range<br>of Services, For The Newly Emerging<br>Needs of The Medical Community</h1>
<div class="pill green abs" style="left:858px;top:400px;width:198px;height:39px">
  <span class="ico" style="width:39px;height:39px"><svg width="18" height="18" viewBox="0 0 18 18"><path d="M3 9l4 4 8-9" fill="none" stroke="#8cc63f" stroke-width="3"/></svg></span>CALL US TODAY
</div>

<h2 class="section-title about-title abs">ABOUT <span>VEL-CORA SOLUTIONS</span></h2>
<div class="about-copy abs">
  <p><u>Vel-Cora</u> is an investment company put together by a group of<br>seasoned business professionals who have come together to combine<br>decades of success in the real estate development, management,<br>financing and medical services. The company will be a full service<br>company offering turnkey solutions for medical professionals.</p>
  <p>Vel-Cora will focus on providing a full range of services via a group of<br>distinct companies to deliver newly emerging needs of the medical<br>community. The end goal will be to create complete solutions for<br>individuals in the medical community. Our group has experience and<br>success with the conceptualization, construction and financing of<br>medical and dental clinic spaces.</p>
</div>
<div class="pill abs" style="left:142px;top:986px;width:170px;height:40px">
  <span class="ico"><svg width="18" height="18" viewBox="0 0 18 18"><path d="M3 9l4 4 8-9" fill="none" stroke="#8cc63f" stroke-width="3"/></svg></span>READ MORE
</div>
<div class="about-visual abs" role="img" aria-label="Business team meeting photo in blue tones"></div>

<section class="solutions abs" role="img" aria-label="Faint hospital corridor with medical staff walking"></section>
<h2 class="section-title center abs" style="top:1218px">VEL-CORA SOLUTIONS</h2>
<svg class="abs" style="left:199px;top:1300px" width="315" height="360" role="img" aria-label="Hand touching glowing financial data icons">
  <defs>
    <radialGradient id="hx1" cx=".5" cy=".5" r=".65">
      <stop offset="0" stop-color="#f3f1c2"/><stop offset=".3" stop-color="#d9d36a"/><stop offset=".6" stop-color="#7fb2b8"/><stop offset="1" stop-color="#7c6aa6"/>
    </radialGradient>
    <radialGradient id="hx1b" cx=".25" cy=".3" r=".4">
      <stop offset="0" stop-color="#6fc2e0" stop-opacity=".8"/><stop offset="1" stop-color="#6fc2e0" stop-opacity="0"/>
    </radialGradient>
  </defs>
  <path d="M128 8Q157.5-9 187 8L287 66Q315 83 315 116V244Q315 277 287 294L187 352Q157.5 369 128 352L28 294Q0 277 0 244V116Q0 83 28 66Z" fill="url(#hx1)"/>
  <path d="M128 8Q157.5-9 187 8L287 66Q315 83 315 116V244Q315 277 287 294L187 352Q157.5 369 128 352L28 294Q0 277 0 244V116Q0 83 28 66Z" fill="url(#hx1b)"/>
</svg>
<h3 class="svc-title abs" style="left:601px;top:1378px">LEASING OPERATIONS</h3>
<p class="svc-copy abs" style="left:601px;top:1425px">Vel-Cora Solutions leasing divison will secure an<br>investment portfolio comprised of equipment leases and<br>other small business financing solutions across Western<br>Canada.</p>
<div class="pill abs" style="left:601px;top:1535px;width:170px;height:40px">
  <span class="ico"><svg width="18" height="18" viewBox="0 0 18 18"><path d="M3 9l4 4 8-9" fill="none" stroke="#8cc63f" stroke-width="3"/></svg></span>KNOW MORE
</div>

<h3 class="svc-title abs" style="left:200px;top:1767px">SECURITY MEASURES</h3>
<p class="svc-copy abs" style="left:200px;top:1814px;font-size:12.8px;letter-spacing:.2px">Vel-Cora Solution leasing divison will implement a number<br>of security measures which ensures investors are secure and<br>returns are maximised over the elife of the investments.</p>
<div class="pill abs" style="left:200px;top:1923px;width:170px;height:40px">
  <span class="ico"><svg width="18" height="18" viewBox="0 0 18 18"><path d="M3 9l4 4 8-9" fill="none" stroke="#8cc63f" stroke-width="3"/></svg></span>KNOW MORE
</div>
<svg class="abs" style="left:699px;top:1691px" width="317" height="357" role="img" aria-label="Open hand holding a glowing security shield in a digital network">
  <defs>
    <radialGradient id="hx2" cx=".5" cy=".45" r=".7">
      <stop offset="0" stop-color="#7fb0e8"/><stop offset=".35" stop-color="#2a62b0"/><stop offset=".75" stop-color="#0f2f6e"/><stop offset="1" stop-color="#08193f"/>
    </radialGradient>
    <radialGradient id="hx2b" cx=".72" cy=".65" r=".3">
      <stop offset="0" stop-color="#c89a86" stop-opacity=".6"/><stop offset="1" stop-color="#c89a86" stop-opacity="0"/>
    </radialGradient>
  </defs>
  <path d="M129 8Q158.5-9 188 8L289 66Q317 83 317 116V241Q317 274 289 291L188 349Q158.5 366 129 349L28 291Q0 274 0 241V116Q0 83 28 66Z" fill="url(#hx2)"/>
  <path d="M129 8Q158.5-9 188 8L289 66Q317 83 317 116V241Q317 274 289 291L188 349Q158.5 366 129 349L28 291Q0 274 0 241V116Q0 83 28 66Z" fill="url(#hx2b)"/>
</svg>

<h2 class="section-title center abs" style="top:2243px">UPCOMING PROJECTS</h2>
<div class="arrow abs" style="left:62px;top:2493px"><svg width="14" height="14" viewBox="0 0 14 14"><path d="M9 2L4 7l5 5" fill="none" stroke="#222" stroke-width="2.2"/></svg></div>
<div class="arrow abs" style="left:1094px;top:2493px"><svg width="14" height="14" viewBox="0 0 14 14"><path d="M5 2l5 5-5 5" fill="none" stroke="#222" stroke-width="2.2"/></svg></div>

<article class="card abs" style="left:142px;top:2313px">
  <div class="photo" role="img" aria-label="Bright warehouse interior with skylights" style="background:linear-gradient(180deg,#7f9fcc 0%,#c7d6ea 35%,#e6edf6 55%,#9fb4d2 75%,#6d87b0)"></div>
  <div class="date"><i></i>MAY 10, 2020</div>
  <h3>PINEGROVE BUSINESS PARK</h3>
  <p>The Pinegrove Business Park in Holtmere, North Province on Kestrel island, is presently under contract.</p>
  <div class="pill sm"><span class="ico"><svg width="14" height="14" viewBox="0 0 18 18"><path d="M3 9l4 4 8-9" fill="none" stroke="#8cc63f" stroke-width="3"/></svg></span>READ MORE</div>
</article>
<article class="card abs" style="left:455px;top:2313px">
  <div class="photo" role="img" aria-label="Historic stone office building facade under blue sky" style="background:linear-gradient(180deg,#2f63c8 0%,#5579b8 18%,#6d5e52 24%,#cdbfa6 40%,#b9a98e 65%,#7e7364 85%,#5d564c)"></div>
  <div class="date"><i></i>MAY 11 2020</div>
  <h3>HOLTMERE BUSINESS PARK</h3>
  <p>The city of Holtmere is a core municipality in the Western Communities.</p>
  <div class="pill sm"><span class="ico"><svg width="14" height="14" viewBox="0 0 18 18"><path d="M3 9l4 4 8-9" fill="none" stroke="#8cc63f" stroke-width="3"/></svg></span>READ MORE</div>
</article>
<article class="card abs" style="left:769px;top:2313px">
  <div class="photo" role="img" aria-label="Business people silhouettes over a city skyline in blue" style="background:radial-gradient(ellipse 90px 120px at 90px 110px,rgba(20,50,110,.7),rgba(20,50,110,0) 70%),radial-gradient(ellipse 80px 120px at 220px 100px,rgba(30,60,120,.6),rgba(30,60,120,0) 70%),linear-gradient(180deg,#8fb4e6,#4f7fc4 50%,#24508f)"></div>
  <div class="date"><i></i>MAY 12, 2020</div>
  <h3 style="font-size:13.5px;left:12px">MT. CORWIN RIDGE PROFESSIONAL</h3>
  <p>Mt. Corwin Professional building will feature a repurposed building adjacent.</p>
  <div class="pill sm"><span class="ico"><svg width="14" height="14" viewBox="0 0 18 18"><path d="M3 9l4 4 8-9" fill="none" stroke="#8cc63f" stroke-width="3"/></svg></span>READ MORE</div>
</article>
<div class="pill abs" style="left:514px;top:2755px;width:171px;height:41px">
  <span class="ico" style="width:41px;height:41px"><svg width="18" height="18" viewBox="0 0 18 18"><path d="M3 9l4 4 8-9" fill="none" stroke="#8cc63f" stroke-width="3"/></svg></span>VIEW ALL
</div>

<section class="team abs" role="img" aria-label="Faint hospital hallway with staff in green tint"></section>
<h2 class="section-title center abs" style="top:2978px;color:var(--white)">OUR TEAM</h2>
<div class="tab abs" style="left:400px;top:3059px;width:201px;background:var(--blue);color:var(--white)">MANAGEMENT TEAM</div>
<div class="tab abs" style="left:627px;top:3059px;width:171px;background:var(--white);color:var(--blue)">OUR PARTNERS</div>
<div class="arrow abs" style="left:62px;top:3224px"><svg width="14" height="14" viewBox="0 0 14 14"><path d="M9 2L4 7l5 5" fill="none" stroke="#222" stroke-width="2.2"/></svg></div>
<div class="arrow abs" style="left:1094px;top:3224px"><svg width="14" height="14" viewBox="0 0 14 14"><path d="M5 2l5 5-5 5" fill="none" stroke="#222" stroke-width="2.2"/></svg></div>

<div class="person abs" style="left:142px;top:3157px">
  <svg class="portrait" viewBox="0 0 157 170" role="img" aria-label="Portrait of Gil Parish">
    <defs><linearGradient id="pt1" x1="0" y1="0" x2="0" y2="1"><stop offset="0" stop-color="#8f8c8a"/><stop offset=".45" stop-color="#c9a08a"/><stop offset=".7" stop-color="#e9e9ec"/><stop offset="1" stop-color="#b8bcc4"/></linearGradient></defs>
    <path d="M64 5Q78-3 92 5L145 35Q157 43 157 57V113Q157 127 145 135L92 165Q78 173 64 165L12 135Q0 127 0 113V57Q0 43 12 35Z" fill="url(#pt1)"/>
  </svg>
  <h4>GIL PARISH</h4><div class="role">DESIGNATION</div>
  <p>Lorem Ipsum is simply dummy of the printing &amp; typesetting industry Lorem Ipsum has typesetting</p>
  <div class="badge"></div>
</div>
<div class="person abs" style="left:623px;top:3157px">
  <svg class="portrait" viewBox="0 0 157 170" role="img" aria-label="Portrait of Dietmar Vellasquin outdoors">
    <defs><linearGradient id="pt2" x1="0" y1="0" x2="0" y2="1"><stop offset="0" stop-color="#9dc2e4"/><stop offset=".35" stop-color="#eef1f4"/><stop offset=".6" stop-color="#b07f66"/><stop offset="1" stop-color="#2b3a4c"/></linearGradient></defs>
    <path d="M64 5Q78-3 92 5L145 35Q157 43 157 57V113Q157 127 145 135L92 165Q78 173 64 165L12 135Q0 127 0 113V57Q0 43 12 35Z" fill="url(#pt2)"/>
  </svg>
  <h4>DIETMAR VELLASQUIN</h4><div class="role">DESIGNATION</div>
  <p>Lorem Ipsum is simply dummy of the printing &amp; typesetting industry Lorem Ipsum has typesetting</p>
  <div class="badge"></div>
</div>

<h2 class="section-title center abs" style="top:3538px">SUBSCRIBE TO OUR NEWSLETTER</h2>
<p class="center abs" style="top:3590px;font-size:14.5px;color:#333">Sign up to get the latest &nbsp;News, &nbsp;releases and more ...</p>
<div class="news-input abs">Email Here</div>
<div class="news-btn abs">JOIN MAILING LIST</div>

<footer class="site-footer abs">
  <div class="brand abs">VEL-CORA<small>SOLUTIONS</small></div>
  <p class="foot-about abs"><u>Vel-Cora</u> is an investment company put together by a group of seasoned business professionals who have come together. [+]</p>
  <div class="abs" style="left:455px;top:77px">
    <div class="col-h">QUICK LINKS</div>
    <ul class="list" style="margin-top:14px"><li>Home</li><li>About Us</li><li>What We Do</li><li>Contact Us</li></ul>
  </div>
  <div class="abs" style="left:667px;top:77px;width:240px">
    <div class="col-h">CONTACT DETAILS</div>
    <div class="contact-row" style="margin-top:18px;padding-left:20px;position:relative">
      <svg style="position:absolute;left:0;top:3px" width="11" height="14" viewBox="0 0 11 14"><path d="M5.5 0A5.5 5.5 0 0 0 0 5.5C0 9 5.5 14 5.5 14S11 9 11 5.5A5.5 5.5 0 0 0 5.5 0z" fill="#fff"/><circle cx="5.5" cy="5.5" r="2" fill="#0355a3"/></svg>
      123, Building Name, Street<br>City, State 123456</div>
    <div class="contact-row" style="margin-top:14px;padding-left:20px;position:relative">
      <svg style="position:absolute;left:0;top:3px" width="12" height="12" viewBox="0 0 12 12"><path d="M2 0l3 3-1.5 1.5a7 7 0 0 0 4 4L9 7l3 3-2 2C5 12 0 7 0 2z" fill="#fff"/></svg>
      <b style="font-weight:600">PHONE</b><br>123.456.7890</div>
    <div class="contact-row" style="margin-top:14px;padding-left:20px;position:relative">
      <svg style="position:absolute;left:0;top:5px" width="13" height="9" viewBox="0 0 13 9"><rect width="13" height="9" fill="#fff"/><path d="M0 0l6.5 5L13 0" fill="none" stroke="#0355a3"/></svg>
      <b style="font-weight:600">EMAIL</b><br>support@velcorahealth.ca</div>
  </div>
  <div class="abs" style="left:945px;top:77px">
    <div class="col-h">FOLLOW US</div>
    <div style="margin-top:12px">
      <div class="social"><i></i>Friendline</div>
      <div class="social"><i></i>Chirpnet</div>
      <div class="social"><i></i>Vidstream</div>
      <div class="social"><i></i>Workweb</div>
    </div>
  </div>
</footer>
<div class="copyright abs">Copyright © 2020 VEL-CORA SOLUTION. All Rights Reserved.</div>

</body>
</html>
```